My project benefits Military, First Responders, Police, Fire, and Educators.

Contact Information for Business Card

2 Sided appointment card. Visual side will have my head shot with "Brisk Lantern" in a bold graffic/text. I am picturing maybe the headshot applied to a filter that has a matrix effect where the picture is made up of data/numbers flowing vertically through the photo. I am of course open to other concepts as well. Side two will have contact info presented in an attractive visual complimenting the front.

```html
<!DOCTYPE html>
<html lang="en">
<head>
<meta charset="utf-8">
<title>Brisk Lantern – Appointment Card</title>
<link href="https://fonts.googleapis.com/css2?family=Open+Sans:ital,wght@0,400;0,600;0,700;1,600&display=swap" rel="stylesheet">
<style>
  :root {
    --stage: #ecebe9;
    --card-grey: #58595b;
    --band-black: #1c1c1c;
    --brand-red: #c8161d;
    --white: #ffffff;
    --ink: #222222;
    --rule: #8a8a8a;
    --photo-dark: #2a2f3a;
    --photo-mid: #6b7280;
  }
  * { margin: 0; padding: 0; box-sizing: border-box; }
  html, body { width: 1200px; height: 900px; overflow: hidden; }
  body {
    background: var(--stage);
    font-family: "Open Sans", Arial, sans-serif;
    position: relative;
  }
  .card { position: absolute; box-shadow: 0 6px 18px rgba(0,0,0,.18); overflow: hidden; }

  /* Front */
  .card-front {
    left: 78px; top: 35px; width: 588px; height: 363px;
    background: var(--card-grey);
  }
  .headshot {
    position: absolute; left: 0; top: 0; width: 330px; height: 363px;
    background: linear-gradient(180deg, var(--photo-mid) 0%, #7d6f66 35%, var(--photo-dark) 75%, #1d2433 100%);
  }
  .wordmark {
    position: absolute; display: flex; align-items: center; gap: 12px;
    font-weight: 700; color: var(--brand-red); letter-spacing: 2px; line-height: 1;
  }
  .wordmark .mark-dot {
    width: 36px; height: 36px; border-radius: 50%; background: var(--brand-red); flex: none;
  }
  .card-front .wordmark { right: 38px; top: 96px; font-size: 40px; }
  .identity { position: absolute; right: 40px; top: 194px; text-align: right; }
  .identity .person-name { color: var(--brand-red); font-size: 20px; font-weight: 600; line-height: 28px; }
  .identity .person-role { color: var(--white); font-size: 16px; line-height: 22px; }
  .contact-list { position: absolute; right: 40px; top: 266px; list-style: none; }
  .contact-list li {
    display: flex; align-items: center; justify-content: flex-end; gap: 8px;
    color: var(--white); font-size: 15px; line-height: 21px;
  }
  .contact-list svg { width: 11px; height: 11px; fill: var(--brand-red); flex: none; }

  /* Back */
  .card-back {
    left: 388px; top: 505px; width: 567px; height: 352px;
    background: var(--white);
  }
  .brand-band {
    height: 134px; background: var(--band-black);
    display: flex; align-items: center; justify-content: center;
  }
  .brand-band .wordmark { position: static; font-size: 38px; }
  .appointment { text-align: center; color: var(--ink); }
  .appointment .lead { font-size: 16px; margin-top: 36px; line-height: 20px; }
  .appointment .title { font-size: 29px; color: var(--brand-red); line-height: 40px; margin-top: 4px; }
  .write-line { position: absolute; left: 38px; width: 493px; height: 1px; background: var(--rule); }
  .write-line.first { top: 266px; }
  .write-line.second { top: 302px; }
  .notice {
    position: absolute; left: 0; right: 0; top: 315px; text-align: center;
    font-size: 13px; font-style: italic; font-weight: 600; color: var(--ink);
  }
</style>
</head>
<body>

<section class="card card-front" aria-label="Card front">
  <div class="headshot" role="img" aria-label="Headshot of the managing director in a dark suit and striped tie"></div>
  <div class="wordmark"><span class="mark-dot"></span><span>BRISK LANTERN</span></div>
  <div class="identity">
    <p class="person-name">Daniel Reyes</p>
    <p class="person-role">Managing Director</p>
  </div>
  <ul class="contact-list">
    <li>555-014-2290
      <svg viewBox="0 0 24 24" aria-hidden="true"><path d="M6.6 10.8a15.1 15.1 0 0 0 6.6 6.6l2.2-2.2a1 1 0 0 1 1-.25 11.4 11.4 0 0 0 3.6.6 1 1 0 0 1 1 1V20a1 1 0 0 1-1 1A17 17 0 0 1 3 4a1 1 0 0 1 1-1h3.5a1 1 0 0 1 1 1c0 1.25.2 2.45.6 3.6a1 1 0 0 1-.25 1z"/></svg>
    </li>
    <li>hello@brisklantern.com
      <svg viewBox="0 0 24 24" aria-hidden="true"><path d="M2 5h20v14H2z M2 5l10 8 10-8" /></svg>
    </li>
    <li>www.brisklantern.com
      <svg viewBox="0 0 24 24" aria-hidden="true"><path d="M10 14 L14 10 M8 12 L5 15 a3 3 0 0 0 4 4 l3-3 M16 12 l3-3 a3 3 0 0 0-4-4 l-3 3" stroke="#c8161d" stroke-width="2.5" fill="none"/></svg>
    </li>
  </ul>
</section>

<section class="card card-back" aria-label="Card back">
  <div class="brand-band">
    <div class="wordmark"><span class="mark-dot"></span><span>BRISK LANTERN</span></div>
  </div>
  <div class="appointment">
    <p class="lead">Your&nbsp; Next</p>
    <p class="title">Appointment :</p>
  </div>
  <div class="write-line first"></div>
  <div class="write-line second"></div>
  <p class="notice">Please give 24 hours notice if you need to reschedule your appointment</p>
</section>

</body>
</html>
```